A new presentation to our clients

we are a Real Estate agency, our website is www.lumibrasa.com and it’s time to have a new, fashion and remarcable Business Card. we want to differentiate ourselves from other companies so we want a business card that differentiates us. we want the business card to impact our customers. in the competitive market that we have today, we have to be different and it is this difference that we seek

Target Market(s)

Real Estate Clients

Contact Information for Business Card

We search a totaly diferent card from the usual

Font styles to use
Sans Serif

Colors
e34197

Requirements
Must have
• Logo, adress, phone contact, e-mail, photo, and our website
Nice to have
• We would like to see a modern business card
Should not have
• Houses or building draws

```html
<!DOCTYPE html>
<html lang="pt">
<head>
<meta charset="utf-8">
<title>Lumi Brasa — Business Card</title>
<link rel="stylesheet" href="https://fonts.googleapis.com/css2?family=Roboto:wght@400;500;700&display=swap">
<style>
  :root {
    --stage: #1e1e1e;
    --brand-pink: #e9256b;
    --card-white: #ffffff;
    --ink-light: #ffffff;
  }
  html, body {
    margin: 0;
    padding: 0;
    width: 1200px;
    height: 791px;
    overflow: hidden;
    background: var(--stage);
    font-family: "Roboto", Arial, sans-serif;
  }
  .card {
    position: absolute;
    left: 158px;
    top: 142px;
    width: 882px;
    height: 503px;
    background: var(--card-white);
    display: flex;
    box-shadow: 0 4px 16px rgba(0,0,0,0.45);
  }
  .card__contact {
    position: relative;
    width: 389px;
    height: 100%;
    background: var(--brand-pink);
    color: var(--ink-light);
  }
  .person {
    position: absolute;
    left: 49px;
    top: 110px;
  }
  .person__name {
    margin: 0;
    font-size: 30px;
    font-weight: 700;
    letter-spacing: 0.3px;
    line-height: 1;
  }
  .person__role {
    margin: 6px 0 0 1px;
    font-size: 20px;
    font-weight: 500;
    line-height: 1;
  }
  .address {
    position: absolute;
    left: 49px;
    top: 205px;
    margin: 0;
    font-style: normal;
    font-size: 20px;
    line-height: 27px;
  }
  .contact-list {
    position: absolute;
    left: 50px;
    top: 276px;
    margin: 0;
    padding: 0;
    list-style: none;
    font-size: 20px;
  }
  .contact-list li {
    display: flex;
    align-items: center;
    height: 27.7px;
  }
  .contact-list svg {
    width: 18px;
    height: 18px;
    margin-right: 15px;
    fill: var(--ink-light);
    flex: none;
  }
  .card__brand {
    flex: 1;
    display: flex;
    align-items: center;
    justify-content: center;
  }
  .brand-name {
    font-size: 58px;
    font-weight: 500;
    color: var(--brand-pink);
    letter-spacing: 1px;
    margin-top: -18px;
  }
</style>
</head>
<body>
  <section class="card">
    <div class="card__contact">
      <div class="person">
        <h1 class="person__name">RUI ALMEIDA</h1>
        <p class="person__role">CEO/FOUNDER</p>
      </div>
      <address class="address">
        Rua das Flores Novas, 118<br>
        4400-250, Vila Nova de Gaia
      </address>
      <ul class="contact-list">
        <li>
          <svg viewBox="0 0 24 24" aria-hidden="true"><path d="M6.6 10.8a15.1 15.1 0 0 0 6.6 6.6l2.2-2.2a1 1 0 0 1 1-.25 11.4 11.4 0 0 0 3.6.57 1 1 0 0 1 1 1V20a1 1 0 0 1-1 1A17 17 0 0 1 3 4a1 1 0 0 1 1-1h3.5a1 1 0 0 1 1 1c0 1.25.2 2.45.57 3.57a1 1 0 0 1-.25 1z"/></svg>
          (+351) 220 480 615
        </li>
        <li>
          <svg viewBox="0 0 24 24" aria-hidden="true"><path d="M6 2h9l3 3v5H6z M3 11h18v9H3z M5 21h14v2H5z"/><rect x="6" y="14" width="12" height="1.6" fill="#e9256b"/></svg>
          (+351) 220 480 616
        </li>
        <li>
          <svg viewBox="0 0 24 24" aria-hidden="true"><path d="M2 5h20v14H2z"/><path d="M2.5 5.5 12 13l9.5-7.5" fill="none" stroke="#e9256b" stroke-width="1.8"/></svg>
          geral@lumibrasa.com
        </li>
        <li>
          <svg viewBox="0 0 24 24" aria-hidden="true"><circle cx="12" cy="12" r="10"/><path d="M8 6c2 1 3 3 1 5s1 3 3 4M15 4c-1 2 1 3 3 3M14 19c1-2 3-2 4-1" fill="none" stroke="#e9256b" stroke-width="1.8"/></svg>
          www.lumibrasa.com
        </li>
      </ul>
    </div>
    <div class="card__brand">
      <span class="brand-name">Lumi Brasa</span>
    </div>
  </section>
</body>
</html>
```